Wordpress Theme for Medical Clinics

** Please view updated Sitemap2.pdf doc to clarify some confusion ***

This is a multiuser WordPress subscription site for medical clinics. Please see attachment for sitemap. Please do not include extra content like social media icons, search bars, or images. If you have questions, please ask for clarification.
The site contains the following pages and sub-pages:

1. Home
2. Our Clinic
2a. Our Clinic > Mission
2b. Our Clinic > Services
2c. Our Clinic > Clinic Policies
2d. Our Clinic > Schedules
3. Our Staff
3a. Our Staff > [Staff member page]
4. Resources
4a. Resources > Patient Health (index)
4b. Resources > Patient Health (index) > [post]
4c. Resources > Links
4d. Resources > Forms
5. Alerts
5a. Alerts > [Alert Page]
6. Contact Us

Includes the Following Pages, Subpages, and Content
1. Home
a. About Us
b. Our Staff
c. Bulletins
d. Accepting New Patients (shown as an alert widget)
e. Links
i. Physician Toolbox
ii. Book an Appointment
f. Clinic Policies
i. Show first 3 policies (e.g. Late Arrivals, Missed Appointments, Fees)
ii. Link to Clinic Policies page
g. Primary widget (displayed on all pages)
i. Hours of operation
ii. Contact Info
1. Tel
2. Fax
3. Email
4. Address
5. Get directions (link to Google Maps)
2. Our Clinic
a. Main Page
i. Clinic Name
ii. Overview
iii. Languages Spoken
iv. Secondary Navigation
1. Mission
2. Services
3. Clinic Policies
4. Schedules (see attachment)
b. Our Clinic > Mission
c. Our Clinic > Services
i. For each service include service TITLE and DESCRIPTION
d. Our Clinic > Clinic Policies
i. For each policy include policy TITLE and DESCRIPTION
ii. Include the following policies in mockup
1. Late arrivals
2. Missed appointments
3. Fees for missed appointments
4. Referrals and follow-ups
5. Services not covered by RDA
6. Information for LTF patients
7. Medical Legal Reports
e. Our Clinic > Schedules
3. Our Staff
a. Main Page
i. Display a list of staff members. Include NAME and DESIGNATION
b. Our Staff > [Staff Name]
i. Include NAME, PICTURE, DESIGNATION, and BIO
4. Resources
a. Resources > Patient Health
i. Main Page
1. Posts (ordered by date)
a. Title
b. Summary
2. Side Navigation
a. Post Categories
ii. Patient Health > [post title]
1. Title
2. Post Category
3. Date
4. Author
5. Summary
6. Body
b. Resources > Links
1. Secondary Navigation - Categories
a. Sample Categories:
i. Local Services
ii. RDA and Drug Coverage
iii. Mental Health Resources
2. Category page
a. Include the following links in the 'Local Services' category
i. Hypertension clinics
ii. Home Care services
iii. Vaccine Clinics
c. Resources > Forms
i. Display a table with form TITLE and CATEGORY
ii. Side Navigation
1. Form Categories
a. Use the following sample Categories
i. Referrals
ii. Insurance
iii. Intake
iv. Discharge
v. Waivers
5. Alerts
a. Main page
i. List of all Alert posts
1. Include post TITLE as a link to the post
ii. Side Navigation
1. Alerts Archive
a. shown as Month + Number of posts
iii. Alerts > [Alert page]
1. Include TITLE, DATE, AUTHOR, BODY
6. Contact Us
a. Map
b. Hours of operation
c. Address
d. Phone number
e. Fax number
e. Fax number
f. Map
g. Email

Design notes:
- fixed width
- responsive (need designs for mobile, tablet, and desktop)
- simple, dark font, white background
- use Font Awesome icons where needed
- user adds own logo

Target Market(s)

Medical Clinics

Industry/Entity Type

Medical

Number of Pages Required

5+ page

Font styles to use
Serif
Sans Serif

Requirements
Must have
• Please keep designs very simple.
• Examples:
• https://www.quolbin.com/install
• http://www.ventrohax.com/company/about-us
• http://brindlequota.org/
• http://www.trosk.com/
Should not have
• Minimal or no use of shadows and gradients

```html
<!DOCTYPE html>
<html lang="en">
<head>
<meta charset="utf-8">
<title>Carewell – Cardiac Clinic</title>
<link href="https://fonts.googleapis.com/css2?family=Open+Sans:wght@400;600;700&display=swap" rel="stylesheet">
<style>
:root{
  --canvas:#ececec;
  --page:#ffffff;
  --brand:#1a7bc9;
  --ink:#2d2d2d;
  --body:#7c8593;
  --muted:#9aa0a8;
  --rule:#e3e5e8;
  --footer:#333436;
  --footer-base:#2a2b2d;
  --footer-text:#c9cbce;
}
*{box-sizing:border-box;margin:0;padding:0}
html,body{width:1000px;height:1200px;overflow:hidden}
body{background:var(--canvas);font-family:"Open Sans",Arial,sans-serif;color:var(--ink);position:relative}
.page{position:absolute;left:62px;top:0;width:875px;height:1200px;background:var(--page)}
.abs{position:absolute}
a{color:inherit;text-decoration:none}

.topbar{left:0;top:0;width:875px;height:24px;border-top:2px solid #cfe3f2;border-bottom:1px solid var(--rule);font-size:8px;color:var(--muted)}
.topbar .left{left:62px;top:6px}
.topbar .left b{color:#555;font-weight:600;margin-right:4px}
.topbar .right{right:64px;top:6px;display:flex;gap:14px;align-items:center}
.topbar .right span{display:flex;align-items:center;gap:5px}

.header{left:0;top:24px;width:875px;height:58px;border-bottom:1px solid #dcdcdc}
.brand{display:flex;align-items:center;gap:8px;font-size:21px;color:#222}
.brand i{width:32px;height:32px;border-radius:50%;background:var(--brand);display:block}
.header .brand{left:62px;top:12px}
.nav{right:63px;top:0;display:flex;gap:24px;font-size:11px;font-weight:400;color:#222}
.nav a{padding-top:20px;height:58px}
.nav a.active{color:var(--brand);border-top:2px solid var(--brand);padding-top:18px}

.titlebar{left:62px;top:82px;width:751px;height:51px;border-bottom:1px solid var(--rule)}
.titlebar h1{position:absolute;left:0;top:15px;font-size:16px;font-weight:400;color:var(--brand)}
.titlebar .accent{position:absolute;left:0;bottom:-1px;width:57px;height:2px;background:var(--brand)}
.crumbs{position:absolute;left:80px;top:21px;font-size:8px;color:#777}
.crumbs a{text-decoration:underline}

.sidebar{left:62px;top:156px;width:175px}
.sidebar h3{font-size:12px;font-weight:400;color:#333;margin-bottom:8px}
.sidebar li{list-style:none;height:25.5px;border-bottom:1px solid #eceef0;font-size:8.5px;color:#888;display:flex;align-items:center;gap:7px}
.sidebar li.current{color:var(--brand)}
.sidebar svg{flex:none}

.content{left:296px;top:164px;width:482px}
.content h2{font-size:23px;font-weight:400;color:#333;padding-bottom:13px;border-bottom:1px solid var(--rule);position:relative}
.content h2::after{content:"";position:absolute;left:0;bottom:-1px;width:49px;height:2px;background:var(--brand)}
.content h4{font-size:9.5px;font-weight:700;color:#222;margin:30px 0 5px}
.content p{font-size:8.2px;line-height:13px;color:var(--body);margin-bottom:5px}

.footer{left:0;top:870px;width:875px;height:280px;background:var(--footer);color:var(--footer-text);font-size:8.5px}
.footer .brand{position:absolute;left:62px;top:38px;color:#fff}
.footer h5{position:absolute;font-size:9.5px;font-weight:600;color:#fff;letter-spacing:.2px}
.fcol{position:absolute;line-height:14px}
.contact-row{display:flex;gap:10px;margin-bottom:14px;font-size:8px}
.contact-row svg{flex:none;margin-top:2px}
.links li{list-style:none;margin-bottom:6px;color:#fff;font-size:9px}
.links li::before{content:"›";margin-right:9px}
.tweet{display:flex;gap:6px;margin-bottom:10px}
.tweet b{color:#fff;font-weight:400}
.tweet em{display:block;color:#3aa0e8;font-style:normal;font-size:7.5px;margin-top:3px}
.subscribe{display:flex;margin-top:12px}
.subscribe span{width:114px;height:19px;background:#e9eaeb;color:#9a9a9a;font-size:8px;padding:4px 7px}
.subscribe b{width:56px;height:19px;background:var(--brand);color:#fff;font-weight:400;font-size:8.5px;text-align:center;line-height:19px}
.baseline{left:0;top:1150px;width:875px;height:50px;background:var(--footer-base);font-size:7.5px;color:#cfd1d4;padding:19px 62px}
</style>
</head>
<body>
<div class="page">

  <div class="abs topbar">
    <div class="abs left"><b>Call Us Today!</b> +100 482 310 &nbsp;&nbsp;|&nbsp;&nbsp; contact@carewell.example</div>
    <div class="abs right">
      <span><svg width="9" height="10" viewBox="0 0 9 10"><rect x="1" y="1.5" width="7" height="8" fill="none" stroke="#aaa"/><rect x="3" y="0" width="3" height="2" fill="#aaa"/></svg>Book an Appointment</span>
      <span>|</span>
      <span><svg width="11" height="9" viewBox="0 0 11 9"><rect x=".5" y="2" width="10" height="6.5" fill="none" stroke="#aaa"/><rect x="4" y=".5" width="3" height="2" fill="none" stroke="#aaa"/></svg>Physician Toolbox</span>
    </div>
  </div>

  <header class="abs header">
    <div class="abs brand"><i></i>Carewell</div>
    <nav class="abs nav">
      <a class="active" href="#">Home</a><a href="#">Our Clinic</a><a href="#">Staff</a><a href="#">Resources</a><a href="#">Alerts</a><a href="#">Contact</a>
    </nav>
  </header>

  <div class="abs titlebar">
    <h1>Our clinic</h1><span class="accent"></span>
    <div class="crumbs"><a href="#">Home</a> &nbsp;›&nbsp; Our Clinic</div>
  </div>

  <aside class="abs sidebar">
    <h3>Categories</h3>
    <ul>
      <li class="current"><svg width="12" height="12" viewBox="0 0 12 12"><circle cx="6" cy="6" r="6" fill="#1a7bc9"/><path d="M5 3.5 7.5 6 5 8.5" stroke="#fff" fill="none" stroke-width="1.3"/></svg>Overview</li>
      <li><svg width="12" height="12" viewBox="0 0 12 12"><circle cx="6" cy="6" r="5.5" fill="none" stroke="#999"/><path d="M5 3.5 7.5 6 5 8.5" stroke="#999" fill="none"/></svg>Mission</li>
      <li><svg width="12" height="12" viewBox="0 0 12 12"><circle cx="6" cy="6" r="5.5" fill="none" stroke="#999"/><path d="M5 3.5 7.5 6 5 8.5" stroke="#999" fill="none"/></svg>Services</li>
      <li><svg width="12" height="12" viewBox="0 0 12 12"><circle cx="6" cy="6" r="5.5" fill="none" stroke="#999"/><path d="M5 3.5 7.5 6 5 8.5" stroke="#999" fill="none"/></svg>Schedules</li>
      <li><svg width="12" height="12" viewBox="0 0 12 12"><circle cx="6" cy="6" r="5.5" fill="none" stroke="#999"/><path d="M5 3.5 7.5 6 5 8.5" stroke="#999" fill="none"/></svg>Clinic Policies</li>
    </ul>
  </aside>

  <main class="abs content">
    <h2>Cardiac Clinic</h2>
    <h4>Donec scelerisque leo</h4>
    <p>Integer iaculis egestas odio, vel dictum turpis placerat id ellentesque semper nisl eget odio eleifend, nec blandit libero porta aliquam vel vehicula dui nam sit amet ultricies sapien.<br>Nulla euismod vitae justo a ullamcorper. In rhoncus nisi massa, sit amet tristique augue viverra vitae. Ut vitae lectus quam. Proin aliquet rhoncus magna vel scelerisque. Nulla facilisi. Aliquam ut scelerisque nulla.</p>
    <p>Integer iaculis egestas odio, vel dictum turpis placerat id ellentesque semper nisl eget odio eleifend, nec blandit libero porta aliquam vel vehicula dui nam sit amet ultricies sapien.<br>Nulla euismod vitae justo a ullamcorper. In rhoncus nisi massa, sit amet tristique augue viverra vitae. Ut vitae lectus quam. Proin aliquet rhoncus magna vel scelerisque. Nulla facilisi. Aliquam ut scelerisque nulla.</p>
    <p>Integer iaculis egestas odio, vel dictum turpis placerat id ellentesque semper nisl eget odio eleifend, nec blandit libero porta aliquam vel vehicula dui nam sit amet ultricies sapien.<br>Nulla euismod vitae justo a ullamcorper. In rhoncus nisi massa, sit amet tristique augue viverra vitae. Ut vitae lectus quam. Proin aliquet rhoncus magna vel scelerisque. Nulla facilisi. Aliquam ut scelerisque nulla.</p>
  </main>

  <footer class="abs footer">
    <div class="brand"><i></i>Carewell</div>
    <div class="fcol" style="left:62px;top:82px;width:135px">
      <p style="margin-bottom:16px">Lorem ipsum dolor sit amet, teft consecte tur adipiscing.</p>
      <div class="contact-row"><svg width="8" height="11" viewBox="0 0 8 11"><path d="M4 0a4 4 0 0 1 4 4c0 3-4 7-4 7S0 7 0 4a4 4 0 0 1 4-4z" fill="#c9cbce"/><circle cx="4" cy="4" r="1.5" fill="#333436"/></svg><span>Carewell Clinic<br>48 Alder Lane<br>Brookfield, NY 10290</span></div>
      <div class="contact-row"><svg width="9" height="22" viewBox="0 0 9 22"><path d="M1 1h2l1 2-1 1c.5 1 1.5 2 2.5 2.5l1-1 2 1v2c-4 0-7.5-3.5-7.5-7.5z" fill="#c9cbce"/><rect x="0" y="16" width="9" height="4" fill="#c9cbce"/><rect x="2" y="13" width="5" height="3" fill="#c9cbce"/></svg><span>+100 482 310<br>+100 482 311</span></div>
      <div class="contact-row"><svg width="9" height="7" viewBox="0 0 9 7"><rect width="9" height="7" fill="#c9cbce"/><path d="M0 0l4.5 4L9 0" stroke="#333436" fill="none"/></svg><span style="color:#fff">contact@carewell.example</span></div>
    </div>

    <h5 style="left:249px;top:47px">OUR CLINIC</h5>
    <ul class="fcol links" style="left:250px;top:83px"><li>Mission</li><li>Services</li><li>Schedules</li><li>Policies</li><li>More</li></ul>

    <h5 style="left:437px;top:47px">RESOURCES</h5>
    <div class="fcol" style="left:437px;top:82px;width:170px">
      <div class="tweet"><span>›</span><span>Integer iaculis egestas odio, vel dictum turpis placerat id. Pellentesque semper nisl eget: <b>t.co/Xk7LpQ2aTr</b><em>2 days ago</em></span></div>
      <div class="tweet"><span>›</span><span>Curabitur consequat tortor ut eros posu ere rutrum donec metus nisl, dictum vita fermentum: <b>t.co/Xk7LpQ2aTr</b><em>6 days ago</em></span></div>
    </div>

    <h5 style="left:625px;top:47px">NEWSLETTER</h5>
    <div class="fcol" style="left:625px;top:82px;width:175px">
      <p>Ipsum dolor sit amet, teft consecte tur adipiscing elit ut eunt.</p>
      <div class="subscribe"><span>Email Address</span><b>Subscribe</b></div>
    </div>
  </footer>

  <div class="abs baseline">Copyright 2015 Carewell | All Rights Reserved</div>
</div>
</body>
</html>
```